Hollendorf Business Card

This is the personal business card for Dr Mark Hollendorf and convers three area of his professional activity - all of them involve (foreign) languages:
o QRVB International Ltd - A translation company with 50 staff. Trades internationally
o WideHarbor Ltd - a global online auction marketplace for translation services (startup)
o Tonal Mosaic - cutting edge technology from the brain sciences which helps learners assimilate the sound patterns of a new language (startup)

Target Market(s)

The card needs to have a "cutting edge" feel - but for a fairly conservative audience - academics, investors.

Industry/Entity Type

Business

Requirements
Must have
• Text:
Dr Mark Hollendorf

Co-founder QRVB International Ltd (Language translation)
Founder WideHarbor Ltd (Translation marketplace)
Founder Tonal Mosaic (Language acquisition)

email: mark.oswin@velmora.co.nz
Phone: +64 21 596 3172
Twitter: @MarkOswin7

```html
<!DOCTYPE html>
<html lang="en">
<head>
<meta charset="utf-8">
<title>Dr Mark Hollendorf – Business Card</title>
<link href="https://fonts.googleapis.com/css2?family=Marcellus+SC&family=EB+Garamond:wght@400;700&display=swap" rel="stylesheet">
<style>
  :root {
    --ink: #111111;
    --paper: #ffffff;
    --frame: #000000;
    --rule: #333333;
  }
  * { margin: 0; padding: 0; box-sizing: border-box; }
  html, body {
    width: 1200px;
    height: 686px;
    overflow: hidden;
    background: var(--paper);
  }
  .card {
    position: relative;
    width: 1200px;
    height: 686px;
    background: var(--paper);
    color: var(--ink);
    font-family: "EB Garamond", Georgia, serif;
  }
  .card-frame {
    position: absolute;
    left: 30px;
    top: 30px;
    width: 1140px;
    height: 626px;
    border: 18px solid var(--frame);
  }
  .card-frame::after {
    content: "";
    position: absolute;
    inset: 12px;
    border: 1.5px solid var(--frame);
  }
  .full-name {
    position: absolute;
    left: 124px;
    top: 128px;
    font-family: "Marcellus SC", "Times New Roman", serif;
    font-size: 42px;
    letter-spacing: 3px;
    line-height: 1;
    font-weight: 400;
  }
  .full-name .cap { font-size: 48px; }
  .name-rule {
    position: absolute;
    left: 124px;
    top: 198px;
    width: 984px;
    height: 1.5px;
    background: var(--rule);
  }
  .ventures {
    position: absolute;
    left: 124px;
    top: 212px;
    width: 440px;
    list-style: none;
    font-size: 15px;
    line-height: 23px;
  }
  .ventures li { margin-bottom: 27px; }
  .ventures li:first-child { margin-bottom: 28px; }
  .contact {
    position: absolute;
    left: 124px;
    top: 398px;
    font-size: 23px;
    line-height: 35px;
  }
  .profile {
    position: absolute;
    right: 70px;
    top: 312px;
    text-align: right;
  }
  .profile-name {
    font-size: 24px;
    font-weight: 700;
    line-height: 1;
    margin-right: 70px;
  }
  .profile-role {
    margin-top: 42px;
    font-size: 20px;
    line-height: 1;
  }
</style>
</head>
<body>
  <main class="card">
    <div class="card-frame"></div>

    <h1 class="full-name"><span class="cap">D</span>r. <span class="cap">M</span>ark <span class="cap">H</span>ollendorf</h1>
    <div class="name-rule"></div>

    <ul class="ventures">
      <li>Co-founder QRVB International Ltd (Language<br>Translation)</li>
      <li>Founder WideHarbor Ltd (Translation Marketplace)</li>
      <li>Founder Tonal Mosaic (Language Acquisition)</li>
    </ul>

    <address class="contact" style="font-style: normal;">
      Phone: +64 21 596 3172<br>
      Twitter: @MarkOswin7<br>
      E-mail: mark.oswin@velmora.co.nz
    </address>

    <div class="profile">
      <p class="profile-name">Mark Hollendorf</p>
      <p class="profile-role">Profession in Foreign Languages</p>
    </div>
  </main>
</body>
</html>
```